Logo + Label Design (Men’s Grooming Brand & Product Packaging)

Design a logo and 2 oz pomade label for Brel, a modern men’s grooming brand focused on clean, high-quality, natural ingredients. The design should establish a bold, masculine, minimalist identity that can later extend to products like shaving gel and body wash.

Key Requirements

Create a primary logo for “Brel” and a core label for the 2 oz pomade jar (screw-top).

Use a clean, modern style — masculine, confident, and approachable (think Dorran’s, Velta, Northfield Kit).

Design for 1–2 color screen printing on solid jar colors (white, black, or navy).

Avoid gradients, foil, or embossing. Must work in black & white.

Provide: vector logo, mockup of the 2 oz jar, color palette (CMYK/RGB/HEX), and font specs.

Winning design may lead to future projects (body wash, shave gel, skincare lines).

Font styles to use
Other font styles liked:
• We like the fonts and design concept in the attached mockup.

Requirements
Should not have
• We want to avoid too much writing or busy designs. We want to avoid having graphics/illustrations embedded in the logo if they will cause the brand to look less classy or sophisticated. We also want the design to look simple and all-American (e.g. Hollister and Vane, Pine Ledger, The KIM, etc). We’d like to give a Pellham & Royce vibe that feels classy and high end.

```html
<!DOCTYPE html>
<html lang="en">
<head>
<meta charset="utf-8">
<title>Brel Men's Hair Pomade Label</title>
<link rel="stylesheet" href="https://fonts.googleapis.com/css2?family=Cinzel:wght@900&family=Poppins:wght@300;400;500;900&display=swap">
<style>
  :root {
    --ink: #000000;
    --paper: #ffffff;
  }
  html, body {
    margin: 0;
    padding: 0;
    width: 1200px;
    height: 1200px;
    overflow: hidden;
    background: var(--paper);
  }
  .label {
    display: block;
    width: 1200px;
    height: 1200px;
  }
  .label__ring { fill: var(--ink); }
  .label__face { fill: var(--paper); }
  .label__ring-text {
    fill: var(--paper);
    font-family: "Poppins", sans-serif;
    font-weight: 400;
    font-size: 42px;
  }
  .label__brand {
    fill: var(--ink);
    font-family: "Poppins", sans-serif;
    font-weight: 900;
    font-size: 390px;
    letter-spacing: -6px;
  }
  .label__product {
    fill: var(--ink);
    font-family: "Cinzel", serif;
    font-weight: 900;
    font-size: 66px;
  }
  .label__scent {
    fill: var(--ink);
    font-family: "Poppins", sans-serif;
    font-weight: 300;
    font-size: 56px;
  }
  .label__band { fill: var(--ink); }
  .label__band-text {
    fill: var(--paper);
    font-family: "Poppins", sans-serif;
    font-weight: 500;
    font-size: 48px;
  }
  .label__weight {
    fill: var(--ink);
    font-family: "Poppins", sans-serif;
    font-weight: 500;
    font-size: 36px;
  }
</style>
</head>
<body>
<svg class="label" viewBox="0 0 1200 1200" xmlns="http://www.w3.org/2000/svg" role="img" aria-label="Brel Men's Hair Pomade label, Fresh and Clean, medium hold, matte finish, net weight 2 ounces">
  <defs>
    <path id="ring-path" d="M 600 1132 A 532 532 0 1 1 600 68 A 532 532 0 1 1 600 1132"/>
    <clipPath id="face-clip">
      <circle cx="600" cy="600" r="504"/>
    </clipPath>
  </defs>

  <circle class="label__ring" cx="600" cy="600" r="596"/>
  <circle class="label__face" cx="600" cy="600" r="504"/>

  <text class="label__ring-text">
    <textPath href="#ring-path" startOffset="50%" text-anchor="middle" textLength="2760" lengthAdjust="spacing">Naturally derived plant &amp; bee-based ingredients | Alcohol Free, Non-Irritating | Formulated to minimize scalp irritation</textPath>
  </text>

  <text class="label__brand" x="600" y="540" text-anchor="middle" textLength="840" lengthAdjust="spacingAndGlyphs">BREL</text>

  <text class="label__product" x="600" y="660" text-anchor="middle" textLength="960" lengthAdjust="spacingAndGlyphs">MENS HAIR POMADE</text>

  <text class="label__scent" x="600" y="752" text-anchor="middle">Fresh &amp; Clean</text>

  <rect class="label__band" x="96" y="808" width="1008" height="72" clip-path="url(#face-clip)"/>
  <text class="label__band-text" x="600" y="861" text-anchor="middle">Medium Hold – Matte Finish</text>

  <text class="label__weight" x="600" y="1000" text-anchor="middle">NET WT 2 oz (57 g)</text>
</svg>
</body>
</html>
```